Larvik GmbH needs a sensational homepage!

A draft of the performances and the logo were uploaded in the attachment. The homepage should be adapted to the colors of the logo. Either pictures, graphics or icons of the respective topic are to be used for the buttons. Social media Linkedin, Youtube, Instagram should not be missing. An imprint, contact form with telephone number and email address should be given on the home page. The page should definitely be designed to be responsive for all end devices. Texts as well as images and videos are inserted in the sub-menus or pages. Only the structure and a simple application should be given. We have already secured the domain www.larvik-demo.at.
We are a young, dynamic company with a high technical affinity. Ask for creative suggestions. If something is needed, please contact us.

Target Market(s)

Construction industry, client

Requirements
Must have
• see description
Should not have
• shouldn't be colorful and playful

```html
<!DOCTYPE html>
<html lang="en">
<head>
<meta charset="utf-8">
<title>Larvik GmbH</title>
<link rel="stylesheet" href="https://fonts.googleapis.com/css2?family=Marcellus&family=Roboto:wght@400;500;700&display=swap">
<style>
:root{
  --ink:#2c3a3f;
  --teal:#2f4247;
  --text:#4a4f52;
  --muted:#8a8f92;
  --light:#f1f1f1;
  --contact:#8f9294;
  --white:#ffffff;
}
*{box-sizing:border-box;margin:0;padding:0}
html,body{width:1200px;height:2424px;overflow:hidden;background:var(--white)}
body{position:relative;font-family:'Roboto',Arial,sans-serif;color:var(--text)}

.site-header{position:absolute;left:0;top:0;width:1200px;height:100px}
.brand{position:absolute;left:112px;top:26px;width:170px;height:48px;border:2px solid var(--ink);display:flex;align-items:center;justify-content:center;font-family:'Marcellus',Georgia,serif;font-size:30px;letter-spacing:4px;color:var(--ink)}
.main-nav{position:absolute;right:120px;top:36px;display:flex;align-items:center;gap:22px;font-size:14px;color:var(--ink);font-weight:500}
.main-nav .caret::after{content:"";display:inline-block;margin-left:5px;border:4px solid transparent;border-top:5px solid var(--ink);vertical-align:-2px}
.phone-btn{background:var(--teal);color:var(--white);padding:8px 16px;border-radius:3px;display:flex;align-items:center;gap:8px;font-weight:500}

.hero{position:absolute;left:108px;top:100px;width:1044px;height:590px;background:linear-gradient(180deg,#4d6a85 0%,#8c8f98 35%,#c99a6a 70%,#6b5442 100%)}
.hero-content{position:absolute;left:0;right:0;top:170px;text-align:center;color:var(--white)}
.hero h1{font-family:'Marcellus',Georgia,serif;font-weight:400;font-size:56px;letter-spacing:5px}
.hero p{width:440px;margin:10px auto 0;font-size:16px;font-weight:500;line-height:1.45}
.btn{display:inline-flex;align-items:center;gap:8px;background:var(--teal);color:var(--white);font-size:13px;font-weight:700;letter-spacing:1px;padding:12px 20px;border-radius:2px}
.hero .btn{margin-top:22px}

.about{position:absolute;left:0;top:760px;width:1200px;height:460px}
.about-photo{position:absolute;left:112px;top:5px;width:433px;height:445px;background:linear-gradient(160deg,#c4d3de 0%,#8a949c 50%,#4a4642 100%)}
.about-text{position:absolute;left:620px;top:90px;width:470px}
.section-title{font-family:'Marcellus',Georgia,serif;font-weight:400;font-size:40px;letter-spacing:3px;color:var(--ink)}
.section-title span{color:var(--muted)}
.about-text p{margin-top:16px;font-size:14px;line-height:1.6}
.about-text .btn{margin-top:28px}

.services{position:absolute;left:0;top:1300px;width:1200px;height:580px;background:var(--light)}
.services .section-title{position:absolute;top:40px;left:0;right:0;text-align:center}
.service-card{position:absolute;top:128px;width:310px;height:340px}
.service-card .label{position:absolute;left:0;right:0;bottom:16px;text-align:center;color:var(--white);font-size:14px;font-weight:500;display:flex;flex-direction:column;align-items:center;gap:6px}
.card-scaffold{left:112px;background:linear-gradient(180deg,#9fb8d2 0%,#7d8b94 60%,#56524d 100%)}
.card-redev{left:445px;background:linear-gradient(180deg,#d7d5cf 0%,#b5b2aa 100%)}
.card-redev .overlay{position:absolute;inset:0;background:rgba(38,52,58,.55);color:var(--white);text-align:center;padding-top:40px}
.card-redev h3{font-size:15px;font-weight:500;margin-top:10px;line-height:1.3}
.card-redev ul{list-style:none;margin-top:14px;font-size:13px;line-height:1.8}
.card-redev .btn{position:absolute;left:50%;transform:translateX(-50%);bottom:22px;padding:9px 18px;font-size:12px}
.card-screed{left:780px;background:linear-gradient(160deg,#eceae6 0%,#bdb6ad 55%,#6f6b66 100%)}

.contact{position:absolute;left:108px;top:1880px;width:1044px;height:450px;background:var(--contact);color:var(--white)}
.contact .section-title{position:absolute;top:36px;left:0;right:0;text-align:center;color:var(--ink)}
.contact-info{position:absolute;left:30px;top:125px;width:360px;font-size:13px}
.info-row{display:flex;gap:14px;margin-bottom:22px}
.info-row h4{font-size:14px;font-weight:700;letter-spacing:.5px}
.info-row p{margin-top:4px;line-height:1.4}
.socials{display:flex;gap:10px;margin-top:8px}
.social{width:30px;height:30px;border-radius:50%;background:var(--teal);display:flex;align-items:center;justify-content:center}
.contact-form{position:absolute;left:460px;top:125px;width:560px;font-size:12px}
.field{border-bottom:1px solid rgba(255,255,255,.8);padding:4px 0 10px;margin-bottom:26px}
.field-row{display:flex;gap:30px}
.field-row .field{flex:1}
.field.message{height:60px}
.submit{float:right;width:160px;justify-content:center}

.site-footer{position:absolute;left:0;top:2370px;width:1200px;text-align:center;font-size:12px;color:var(--text)}
</style>
</head>
<body>

<header class="site-header">
  <div class="brand">LARVIK</div>
  <nav class="main-nav">
    <span>Home</span><span>About</span>
    <span class="caret">Scaffolding</span>
    <span class="caret">Redevelopment</span>
    <span class="caret">Screed &amp; insulation</span>
    <span>Contact</span>
    <span class="phone-btn">
      <svg width="14" height="14" viewBox="0 0 24 24"><path fill="#fff" d="M6.6 10.8a15 15 0 0 0 6.6 6.6l2.2-2.2a1 1 0 0 1 1-.25 11 11 0 0 0 3.6.6 1 1 0 0 1 1 1V20a1 1 0 0 1-1 1A17 17 0 0 1 3 4a1 1 0 0 1 1-1h3.5a1 1 0 0 1 1 1 11 11 0 0 0 .6 3.6 1 1 0 0 1-.25 1z"/></svg>
      123-456-7890
    </span>
  </nav>
</header>

<section class="hero" role="img" aria-label="Construction workers on scaffolding at a building site at sunset">
  <div class="hero-content">
    <h1>LARVIK GMBH</h1>
    <p>Lorem ipsum dolor sit amet, consectetur adipiscing elit, sed do eiusmod tempor.</p>
    <span class="btn">GET STARTED
      <svg width="12" height="12" viewBox="0 0 12 12"><circle cx="6" cy="6" r="6" fill="#fff"/><path d="M5 3.5 7.5 6 5 8.5" stroke="#2f4247" stroke-width="1.6" fill="none"/></svg>
    </span>
  </div>
</section>

<section class="about">
  <div class="about-photo" role="img" aria-label="Engineers in hard hats reviewing plans on a construction site"></div>
  <div class="about-text">
    <h2 class="section-title">ABOUT <span>US</span></h2>
    <p>Lorem ipsum dolor sit amet, consectetur adipiscing elit, sed do eiusmod tempor incididunt ut labore et dolore magna aliqua. Ut enim ad minim veniam, quis nostrud exercitation ullamco laboris nisi ut aliquip ex ea commodo consequat. Duis aute irure dolor in reprehenderit in voluptate velit esse cillum dolore eu fugiat nulla pariatur.</p>
    <span class="btn">MORE ABOUT US
      <svg width="12" height="12" viewBox="0 0 12 12"><circle cx="6" cy="6" r="6" fill="#fff"/><path d="M5 3.5 7.5 6 5 8.5" stroke="#2f4247" stroke-width="1.6" fill="none"/></svg>
    </span>
  </div>
</section>

<section class="services">
  <h2 class="section-title">OUR <span>SERVICES</span></h2>
  <div class="service-card card-scaffold" role="img" aria-label="Scaffolding around a building under construction">
    <div class="label">
      <svg width="22" height="22" viewBox="0 0 22 22" fill="none" stroke="#fff" stroke-width="1.6"><path d="M4 2v18M18 2v18M4 6h14M4 11h14M4 16h14M4 6l14 5"/></svg>
      Scaffolding
    </div>
  </div>
  <div class="service-card card-redev" role="img" aria-label="Bright renovated interior room with arched windows">
    <div class="overlay">
      <svg width="30" height="30" viewBox="0 0 30 30" fill="none" stroke="#fff" stroke-width="1.8"><path d="M4 14 15 5l11 9M7 12v13h16V12"/><rect x="12" y="17" width="6" height="8"/></svg>
      <h3>Redevelopment<br>Project management</h3>
      <ul>
        <li>Concrete repair</li>
        <li>Facade renovation</li>
        <li>Site coordination</li>
        <li>Structural checks</li>
      </ul>
      <span class="btn">INQUIRY</span>
    </div>
  </div>
  <div class="service-card card-screed" role="img" aria-label="Worker in a hard hat applying screed to a floor">
    <div class="label">
      <svg width="22" height="22" viewBox="0 0 22 22" fill="none" stroke="#fff" stroke-width="1.6"><path d="M3 17h12l4-4H7zM11 13V5h4"/></svg>
      Screed &amp; insulation
    </div>
  </div>
</section>

<section class="contact">
  <h2 class="section-title">CONTACT US</h2>
  <div class="contact-info">
    <div class="info-row">
      <svg width="20" height="20" viewBox="0 0 24 24"><path fill="#2f4247" d="M12 2a7 7 0 0 0-7 7c0 5 7 13 7 13s7-8 7-13a7 7 0 0 0-7-7zm0 9.5A2.5 2.5 0 1 1 12 6.5a2.5 2.5 0 0 1 0 5z"/></svg>
      <div><h4>ADDRESS</h4><p>12 Fjordweg, 1010 Wien</p></div>
    </div>
    <div class="info-row">
      <svg width="20" height="20" viewBox="0 0 24 24"><rect x="2" y="5" width="20" height="14" rx="2" fill="#2f4247"/><path d="m3 6 9 7 9-7" stroke="#fff" stroke-width="1.6" fill="none"/></svg>
      <div><h4>E-MAIL</h4><p>hello@larvik-demo.at</p></div>
    </div>
    <div class="info-row">
      <svg width="20" height="20" viewBox="0 0 24 24"><path fill="#2f4247" d="M6.6 10.8a15 15 0 0 0 6.6 6.6l2.2-2.2a1 1 0 0 1 1-.25 11 11 0 0 0 3.6.6 1 1 0 0 1 1 1V20a1 1 0 0 1-1 1A17 17 0 0 1 3 4a1 1 0 0 1 1-1h3.5a1 1 0 0 1 1 1 11 11 0 0 0 .6 3.6 1 1 0 0 1-.25 1z"/></svg>
      <div><h4>Phone</h4><p>123 456 7890</p></div>
    </div>
    <div class="socials">
      <span class="social" role="img" aria-label="Professional network profile" title="Professional network">
        <svg width="16" height="16" viewBox="0 0 24 24" fill="none" stroke="#fff" stroke-width="2.2" stroke-linecap="round"><path d="M10 14a4 4 0 0 0 5.6 0l3-3a4 4 0 0 0-5.6-5.6l-1 1"/><path d="M14 10a4 4 0 0 0-5.6 0l-3 3a4 4 0 0 0 5.6 5.6l1-1"/></svg>
      </span>
      <span class="social" role="img" aria-label="Video channel" title="Video channel">
        <svg width="16" height="16" viewBox="0 0 24 24" fill="none" stroke="#fff" stroke-width="2"><rect x="2" y="6" width="13" height="12" rx="1.5"/><path d="M15 10.5 22 7v10l-7-3.5z" fill="#fff"/></svg>
      </span>
      <span class="social" role="img" aria-label="Photo feed" title="Photo feed">
        <svg width="16" height="16" viewBox="0 0 24 24" fill="none" stroke="#fff" stroke-width="2"><rect x="3" y="4" width="18" height="16" rx="1.5"/><path d="m3 17 6-6 5 5 3-3 4 4"/><circle cx="16" cy="8.5" r="1.5" fill="#fff" stroke="none"/></svg>
      </span>
    </div>
  </div>
  <form class="contact-form">
    <div class="field-row">
      <div class="field">First Name *</div>
      <div class="field">Last Name *</div>
    </div>
    <div class="field-row">
      <div class="field">Phone Number *</div>
      <div class="field">Email Address *</div>
    </div>
    <div class="field message">Message *</div>
    <span class="btn submit">SUBMIT</span>
  </form>
</section>

<footer class="site-footer">© 2021 larvik. All Rights Reserved &nbsp;|&nbsp; Privacy Policy &nbsp;|&nbsp; Imprint</footer>

</body>
</html>
```